Duct Manufacturing Company new to the industry needs business card and stationary design

we are sheet metal duct manufacturers looking for a business card design to fit my new business logo.
nothing to crazy that will date, but want it to stand out from the crowed.
I'm sure you guys will work it out.

Contact Information for Business Card

Glen Marsh
Director

Address
17 Dorwell St
Larkfield NSW 2715

0438 760 514

Sales@flowbend.com.au

Font styles to use
Other font styles liked:
• BankGothic md bt

Requirements
Nice to have
• Like the idea of corner rounded to match logo
• like to keep colours flowing
• font I like sharp square not rounded

```html
<!DOCTYPE html>
<html lang="en">
<head>
<meta charset="utf-8">
<title>Flowbend Industries – Business Card</title>
<link rel="stylesheet" href="https://fonts.googleapis.com/css2?family=Lato:wght@400;700;900&display=swap">
<style>
  :root {
    --backdrop: #8e8d8e;
    --brand-blue: #044a96;
    --brand-green: #7dc242;
    --card-white: #f1f1f1;
    --ink-dark: #1a1a1a;
    --rule-grey: #7d8fb0;
    --web-grey: #b9c3d6;
  }
  * { box-sizing: border-box; margin: 0; padding: 0; }
  html, body {
    width: 1200px; height: 900px; overflow: hidden;
    background: var(--backdrop);
    font-family: "Lato", sans-serif;
  }
  .card {
    position: absolute;
    width: 560px; height: 320px;
    border-radius: 18px;
    overflow: hidden;
    box-shadow: 0 6px 18px rgba(0,0,0,0.35);
  }

  /* Front */
  .card-front { left: 80px; top: 80px; background: var(--brand-blue); }
  .front-brand {
    position: absolute; left: 0; right: 0; top: 118px;
    display: flex; align-items: center; justify-content: center; gap: 12px;
  }
  .brand-dot {
    width: 18px; height: 18px; border-radius: 50%;
    background: var(--brand-green);
    flex: none;
  }
  .front-brand .brand-name {
    font-weight: 900; font-size: 30px; letter-spacing: 2px;
    color: #ffffff; text-transform: uppercase;
  }
  .front-web {
    position: absolute; left: 40px; right: 40px; top: 232px;
    display: flex; align-items: center; gap: 14px;
  }
  .front-web .rule { flex: 1; height: 1px; background: var(--rule-grey); }
  .front-web .web-address { font-size: 15px; color: var(--web-grey); letter-spacing: 0.5px; }

  /* Back */
  .card-back { left: 560px; top: 500px; background: var(--card-white); }
  .contact-band { position: absolute; inset: 0; }
  .back-brand {
    position: absolute; right: 34px; top: 36px;
    display: flex; align-items: center; gap: 8px;
  }
  .back-brand .brand-dot { width: 12px; height: 12px; }
  .back-brand .brand-name {
    font-weight: 900; font-size: 19px; letter-spacing: 1px;
    color: var(--brand-green); text-transform: uppercase;
  }
  .holder { position: absolute; left: 60px; top: 150px; }
  .holder-name { font-weight: 900; font-size: 25px; color: var(--brand-blue); }
  .holder-title { font-size: 15px; color: var(--ink-dark); margin-top: 2px; }
  .contact-list {
    position: absolute; right: 30px; top: 176px;
    list-style: none; text-align: right; color: #ffffff;
    font-size: 15px; line-height: 22px;
  }
  .contact-list li { display: flex; justify-content: flex-end; align-items: center; gap: 7px; }
  .contact-list .icon { width: 13px; height: 13px; fill: none; stroke: #ffffff; stroke-width: 1.6; }
  .contact-list .icon-solid { fill: #ffffff; stroke: none; }
  .contact-list .phone { font-size: 17px; }
</style>
</head>
<body>

<section class="card card-front" aria-label="Business card front">
  <div class="front-brand">
    <span class="brand-dot"></span>
    <span class="brand-name">Flowbend Industries</span>
  </div>
  <div class="front-web">
    <span class="rule"></span>
    <span class="web-address">www.flowbend.com.au</span>
    <span class="rule"></span>
  </div>
</section>

<section class="card card-back" aria-label="Business card back">
  <svg class="contact-band" viewBox="0 0 560 320" preserveAspectRatio="none" aria-hidden="true">
    <polygon points="120,320 560,60 560,320" fill="var(--brand-blue)"/>
  </svg>

  <div class="back-brand">
    <span class="brand-dot"></span>
    <span class="brand-name">Flowbend Industries</span>
  </div>

  <div class="holder">
    <p class="holder-name">Glen Marsh</p>
    <p class="holder-title">Director</p>
  </div>

  <ul class="contact-list">
    <li>17 Dorwell St</li>
    <li>Larkfield NSW 2715</li>
    <li class="phone">0438 760 514
      <svg class="icon icon-solid" viewBox="0 0 16 16" aria-hidden="true"><path d="M3 2h3l1 3-2 1.5a8 8 0 0 0 4.5 4.5L11 9l3 1v3a1 1 0 0 1-1 1A12 12 0 0 1 2 3a1 1 0 0 1 1-1z"/></svg>
    </li>
    <li>Sales@flowbend.com.au
      <svg class="icon" viewBox="0 0 16 16" aria-hidden="true"><rect x="1.5" y="3.5" width="13" height="9"/><path d="M1.5 3.5 8 9l6.5-5.5"/></svg>
    </li>
    <li>www.flowbend.com.au
      <svg class="icon" viewBox="0 0 16 16" aria-hidden="true"><rect x="1.5" y="2.5" width="13" height="9"/><path d="M5 14.5h6M8 11.5v3"/></svg>
    </li>
  </ul>
</section>

</body>
</html>
```